Willow Cradle Pregnancy and Baby Massage

I need a web design for a new business, WILLOW CRADLE PREGNANCY AND BABY MASSAGE that I am in the process of setting up in the suburbs of Perth, Western Australia. The business is owned and operated by myself and my intention is to service Pregnant Mothers and Parents of Young Babies that would benefit from massage. I would like to have a "Home Page" and pages for "About Me", "Pregnancy Massage", "Baby Massage", a Pricing Page for Pregnancy Massage Sessions, a Pricing Page for Baby Massage Sessions, and a "Contact Me" page to allow clients to either contact me with queries or book available pregnancy massage sessions on a particular day of the week. I would also like a "News" page that would include articles I have written, news about new courses and a link to my Facebook page (yet to be set up). I would like to keep the colour schemes similar to my logo design colours. I need the design to be easy to follow and to appeal to a younger audience (20's to mid 30's).
The target audience is pregnant mothers-to-be wishing to receive massage treatments, and new parents and grandparents of small babies that would like to learn how to massage their babies.
The look and feel should be modern, professional, elegant and feminine.
I need the design to be in a standard format such that I can update the content by myself ( and does not need specialised software) as the company and business progresses.

Target Market(s)

Contact Information for Business Card

Card should have rounded edges. Design should have the same "feel" as the website. Contact Details of my business address, mobile phone, email and website should be included.

Font styles to use
Script

Requirements
Must have
• Same colours as logo design. In cmyk system, the colours are: 20,60,0,0 which best result is pantone 681 and 40,40,0,0 which best result is pantone 2645. Card should include the logo design.

```html
<!DOCTYPE html>
<html lang="en">
<head>
<meta charset="utf-8">
<title>Willow Cradle Pregnancy and Baby Massage</title>
<link rel="stylesheet" href="https://fonts.googleapis.com/css2?family=Lato:ital,wght@0,400;1,400&family=Open+Sans:wght@400;600&display=swap">
<style>
  :root {
    --rose: #b86fa6;
    --lavender: #8c83b9;
    --lavender-deep: #6f6891;
    --lavender-soft: #a99bcb;
    --heading: #8a7fb8;
    --ink: #333333;
    --text: #555555;
    --white: #ffffff;
  }
  * { margin: 0; padding: 0; box-sizing: border-box; }
  html, body { width: 1200px; height: 2400px; overflow: hidden; }
  body { position: relative; background: var(--white); font-family: "Open Sans", Arial, sans-serif; color: var(--text); }
  .block { position: absolute; left: 0; width: 1200px; }

  .top-band { top: 0; height: 42px; background: var(--rose); }

  .site-header { top: 42px; height: 115px; background: var(--white); }
  .nav-link { position: absolute; top: 43px; font-size: 19px; color: var(--ink); text-decoration: none; font-family: "Open Sans", Arial, sans-serif; }
  .nav-link.is-active { color: var(--rose); }
  .brand { position: absolute; left: 450px; width: 300px; top: 22px; text-align: center; color: var(--rose); font-family: "Lato", Arial, sans-serif; font-weight: 400; }
  .brand-name { display: block; font-size: 34px; line-height: 40px; }
  .brand-tagline { display: block; font-size: 14px; line-height: 20px; letter-spacing: 0.3px; }

  .hero { top: 157px; height: 582px; background: linear-gradient(135deg, #e9d2c3 0%, #d9b29b 45%, #f1e3d8 100%); }
  .hero-title { position: absolute; left: 0; width: 1200px; top: 430px; text-align: center; font-family: "Open Sans", Arial, sans-serif; font-size: 58px; font-weight: 400; color: var(--ink); letter-spacing: -1px; }
  .hero-sub { position: absolute; right: 170px; top: 505px; font-size: 22px; color: var(--ink); }

  .welcome { top: 739px; height: 314px; text-align: center; }
  .section-title { font-family: "Lato", Arial, sans-serif; font-style: italic; font-weight: 400; color: var(--heading); font-size: 42px; line-height: 50px; }
  .welcome .section-title { position: absolute; top: 40px; width: 100%; }
  .intro { position: absolute; left: 185px; width: 830px; top: 95px; font-size: 15.5px; line-height: 26px; color: var(--text); }
  .service-link { position: absolute; top: 222px; font-family: "Lato", Arial, sans-serif; font-style: italic; font-size: 29px; color: var(--heading); }
  .service-dot { position: absolute; top: 227px; width: 34px; height: 34px; border-radius: 50%; background: var(--rose); }
  .service-divider { position: absolute; left: 586px; top: 216px; width: 2px; height: 50px; background: var(--rose); }

  .benefits { top: 1053px; height: 467px; background: var(--lavender); }
  .benefits-photo { position: absolute; left: 0; top: 0; width: 488px; height: 467px; background: linear-gradient(160deg, #f3ece8 0%, #e3c4ae 55%, #c99a7f 100%); }
  .benefits-copy { position: absolute; left: 581px; top: 50px; width: 470px; color: var(--white); }
  .benefits-copy .section-title { color: var(--white); }
  .benefits-lead { margin-top: 22px; font-size: 16px; line-height: 25px; }
  .benefit-list { list-style: none; font-size: 16px; line-height: 25px; }
  .benefit-list li::before { content: "\2022"; margin: 0 10px 0 4px; }
  .btn-outline { position: absolute; left: 578px; top: 373px; width: 187px; height: 41px; border: 2px solid var(--white); color: var(--white); font-family: "Lato", Arial, sans-serif; font-size: 19px; line-height: 37px; text-align: center; }

  .about { top: 1520px; height: 272px; text-align: center; }
  .about .section-title { position: absolute; top: 37px; width: 100%; }
  .about .intro { left: 155px; width: 890px; top: 96px; }
  .btn-solid { position: absolute; left: 507px; top: 173px; width: 186px; height: 46px; background: var(--rose); color: var(--white); font-family: "Lato", Arial, sans-serif; font-size: 19px; line-height: 46px; text-align: center; }

  .details { top: 1792px; height: 208px; background: linear-gradient(90deg, #a497c6 0%, #c0b3d9 50%, #a497c6 100%); }
  .detail-card { position: absolute; top: 38px; width: 291px; height: 135px; background: rgba(255,255,255,0.35); text-align: center; color: var(--white); }
  .detail-title { margin-top: 20px; font-family: "Lato", Arial, sans-serif; font-style: italic; font-size: 32px; line-height: 38px; color: var(--rose); }
  .detail-text { margin-top: 4px; font-size: 14px; line-height: 24px; padding: 0 20px; }

  .contact { top: 2000px; height: 352px; background: var(--lavender); }
  .contact .section-title { position: absolute; top: 40px; width: 100%; text-align: center; color: var(--white); }
  .field { position: absolute; background: var(--lavender-deep); color: var(--white); font-size: 15px; padding: 10px 8px; }
  .send { position: absolute; left: 243px; top: 266px; width: 722px; height: 40px; background: var(--white); color: var(--rose); text-align: center; line-height: 40px; font-size: 18px; letter-spacing: 1px; }

  .site-footer { top: 2352px; height: 48px; background: var(--rose); color: var(--white); text-align: center; line-height: 48px; font-size: 15px; }
</style>
</head>
<body>
  <div class="block top-band"></div>

  <header class="block site-header">
    <a class="nav-link is-active" style="left:78px">Home</a>
    <a class="nav-link" style="left:166px">About Me</a>
    <a class="nav-link" style="left:288px">benefits</a>
    <div class="brand">
      <span class="brand-name">Willow Cradle</span>
      <span class="brand-tagline">Pregnancy and Baby Massage</span>
    </div>
    <a class="nav-link" style="left:790px">Sessions</a>
    <a class="nav-link" style="left:910px">Testimonials</a>
    <a class="nav-link" style="left:1054px">Contact</a>
  </header>

  <section class="block hero" role="img" aria-label="Hands of expectant parents forming a heart over a pregnant belly, with a photo of sleeping newborn twins">
    <h1 class="hero-title">professional massage service</h1>
    <p class="hero-sub">to pregnant mothers and babies</p>
  </section>

  <section class="block welcome">
    <h2 class="section-title">Welcome To Willow Cradle</h2>
    <p class="intro">Maren is a Practitioner of Pregnancy Massage, and a Paediatric Massage Consultant. She completed her training with Prenatal Touch Institute, and the Infant Touch Learning Service. The ITLS is endorsed by the National College of Birth Carers. The Southern Natural Therapies Society, and accredited by the Association.</p>
    <span class="service-link" style="left:128px">Pregnancy Massage Session</span>
    <span class="service-dot" style="left:506px"></span>
    <span class="service-divider"></span>
    <span class="service-dot" style="left:639px"></span>
    <span class="service-link" style="left:762px">Baby Massage Sessions</span>
  </section>

  <section class="block benefits">
    <div class="benefits-photo" role="img" aria-label="Pregnant woman in a white top making a heart shape with her hands over her belly"></div>
    <div class="benefits-copy">
      <h2 class="section-title">Benefits of Pregnancy Massage</h2>
      <p class="benefits-lead">Pregnancy Massage is a professional relaxation massage that:</p>
      <ul class="benefit-list">
        <li>Reduces anxiety caused by hormonal changes</li>
        <li>Improves circulation</li>
        <li>Reduces muscle aches and pain; muscle and joint conditions such as backache, shoulder and neck pain, hip pain, leg cramps, oedema and carpel tunnel</li>
        <li>Relaxes tense muscle, tones loose muscle and increases muscle flexibility.</li>
      </ul>
    </div>
    <a class="btn-outline">READ MORE</a>
  </section>

  <section class="block about">
    <h2 class="section-title">About Me</h2>
    <p class="intro">Maren is a Practitioner of Pregnancy Massage, and a Paediatric Massage Consultant. She completed her training with Prenatal Touch Institute, and the Infant Touch Learning Service. The ITLS is endorsed by the National College of Birth Carers. The Southern Natural Therapies Society, and accredited by the Guild of Massage Practitioners.</p>
    <a class="btn-solid">READ MORE</a>
  </section>

  <section class="block details" role="img" aria-label="Soft lavender-toned photo of a parent's hands holding a baby">
    <div class="detail-card" style="left:152px">
      <h3 class="detail-title">Address</h3>
      <p class="detail-text">Maren Ellery Willow Cradle Pregnancy and Infant Massage</p>
    </div>
    <div class="detail-card" style="left:454px">
      <h3 class="detail-title">Phone</h3>
      <p class="detail-text">041 5550 192</p>
    </div>
    <div class="detail-card" style="left:757px">
      <h3 class="detail-title">Email</h3>
      <p class="detail-text">maren.ellery@willow-cradle.com.au</p>
    </div>
  </section>

  <section class="block contact">
    <h2 class="section-title">Contact Us</h2>
    <div class="field" style="left:243px;top:106px;width:229px;height:40px">Name</div>
    <div class="field" style="left:490px;top:106px;width:228px;height:40px">E-mail</div>
    <div class="field" style="left:736px;top:106px;width:229px;height:40px">Phone</div>
    <div class="field" style="left:243px;top:165px;width:722px;height:81px">Mesage</div>
    <div class="send">SEND</div>
  </section>

  <footer class="block site-footer">©Willow Cradle - 2017. All Rights Reserved.</footer>
</body>
</html>
```